new branding The Velvet Pour

The Velvet Pour is a Belgian brand of ready to serve mocktails. We're looking for a rebranding of the labels on our bottles (8 different flavours)
Our mocktails are low in sugar, 100% natural and completely alcohol-free. They are also 'ready to serve': gently shake the bottle, serve with ice cubes, finish and your mocktail is ready in no time!
Besides being the ideal aperitif, you can also serve them during brunch or dinner. Thanks to the different flavors, you can pair each mocktail with a dish.
Please visit our website to see the current look&feel: the velvetpour.com - https://thevelvetpour.lumagallery.com/

Target Market(s)

people looking for a premium alcoholfree alternative - premium market

Industry/Entity Type

Mocktails (our mocktails have unique flavors, it's not the non-alcoholic version of a cocktail)

Colors

Designer to choose colors to be used in the design.

Requirements
Must have
• Our brand should be more visible, more recognizable, bolder, without losing the premium and refined character. Base colors should be white, black and silver. The brand should be put more foward. Keep number concept (every mocktail has its number) Put the ingredients/flavours/combinations a bit more forward. make the brand more confident and mature. The eight bottles should become a family. PREMIUM EXPRESSION
Nice to have
• We want to work with a white label. Ideas for the shape of the label Some ideas for the label: Play with shapes, cut outs, texture and number of labels. We like the frosted look and the combination of print & label . Working with 2 labels gives it more dynamic, not one big block Clean label. Working with a cut out shape, can be the logo or the numbers ? Working with 2 labels makes it easier to create an importance of messages. Working with an organic shape makes it unique and give a natural touch Working with a cut out can give a color pop on the white label The label can have parts coming out of the square shape
Should not have
• No crazy stuff, finishes etc should be feasible/realistic

```html
<!DOCTYPE html>
<html lang="en">
<head>
<meta charset="UTF-8">
<title>The Velvet Pour — Basil &amp; Elderflower Label</title>
<link href="https://fonts.googleapis.com/css2?family=Anton&family=Barlow+Condensed:wght@400;500;600&family=Lobster+Two:ital,wght@1,700&display=swap" rel="stylesheet">
<style>
  :root {
    --ink: #151515;
    --paper: #ffffff;
    --backdrop: #e3e3e3;
    --silver: #b9b9b9;
    --rule: #2a2a2a;
  }
  * { box-sizing: border-box; margin: 0; padding: 0; }
  html, body { width: 1200px; height: 1200px; overflow: hidden; }
  body {
    background: var(--backdrop);
    color: var(--ink);
    font-family: "Barlow Condensed", sans-serif;
  }
  .artwork {
    width: 1200px; height: 1200px;
    display: flex; flex-direction: column; align-items: center;
    padding-top: 110px;
  }
  .tagline-arc { width: 640px; height: 140px; display: block; overflow: visible; }
  .tagline-arc text {
    font-family: "Barlow Condensed", sans-serif;
    font-weight: 500; font-size: 24px; letter-spacing: 4px;
    fill: var(--ink);
  }
  .brand-name {
    margin-top: 10px;
    font-family: "Anton", sans-serif;
    font-weight: 400;
    font-size: 118px;
    line-height: 1.02;
    text-align: center;
    text-transform: uppercase;
    letter-spacing: 1px;
    color: var(--ink);
  }
  .serve-badge { margin-top: 50px; width: 150px; height: 150px; display: block; }
  .serve-badge text {
    font-family: "Barlow Condensed", sans-serif;
    font-weight: 500; font-size: 13px; letter-spacing: 1.6px;
    fill: var(--ink);
  }
  .flavour-label {
    margin-top: 50px;
    width: 640px;
    background: var(--paper);
    padding: 10px;
  }
  .flavour-label__frame {
    border: 4px solid var(--ink);
    padding: 22px 36px 18px;
    text-align: center;
  }
  .flavour-name {
    font-family: "Barlow Condensed", sans-serif;
    font-weight: 600; font-size: 58px; line-height: 1;
    text-transform: uppercase; letter-spacing: 0.5px;
  }
  .flavour-note {
    margin-top: 8px;
    font-weight: 500; font-size: 20px; letter-spacing: 1px;
    text-transform: uppercase;
  }
  .label-row {
    display: flex; align-items: stretch; justify-content: space-between;
    border-top: 1.5px solid var(--rule);
  }
  .label-row--specs { margin-top: 14px; padding: 10px 0; }
  .label-row--claims { padding-top: 12px; }
  .label-row__cell {
    flex: 1;
    display: flex; align-items: center; justify-content: center;
  }
  .label-row__cell + .label-row__cell { border-left: 1.5px solid var(--rule); }
  .spec-volume { font-size: 19px; font-weight: 400; justify-content: flex-start; flex: 0 0 120px; }
  .spec-tagline {
    font-family: "Lobster Two", cursive; font-style: italic; font-weight: 700;
    font-size: 26px;
  }
  .spec-number {
    font-family: "Barlow Condensed", sans-serif; font-weight: 600;
    font-size: 52px; line-height: 1; justify-content: flex-end; flex: 0 0 110px;
  }
  .claim { font-size: 19px; font-weight: 400; letter-spacing: 1px; text-transform: uppercase; }
  .claim:first-child { justify-content: flex-start; }
  .claim:last-child { justify-content: flex-end; }
</style>
</head>
<body>
<main class="artwork">
  <svg class="tagline-arc" viewBox="0 0 640 140" aria-label="Premium non-alcoholic drink">
    <defs><path id="tagline-path" d="M 60 130 A 520 520 0 0 1 580 130"/></defs>
    <text text-anchor="middle"><textPath href="#tagline-path" startOffset="50%">PREMIUM NON-ALCOHOLIC DRINK</textPath></text>
  </svg>

  <h1 class="brand-name">The Velvet<br>Pour</h1>

  <svg class="serve-badge" viewBox="0 0 150 150" aria-label="Gently shake the bottle, serve with ice cubes">
    <defs><path id="badge-path" d="M 75 75 m -58 0 a 58 58 0 1 1 116 0 a 58 58 0 1 1 -116 0"/></defs>
    <text><textPath href="#badge-path">GENTLY SHAKE THE BOTTLE · SERVE WITH ICE CUBES ·</textPath></text>
    <circle cx="75" cy="75" r="28" fill="var(--silver)" role="img" aria-label="Leaf icon"/>
  </svg>

  <section class="flavour-label">
    <div class="flavour-label__frame">
      <h2 class="flavour-name">Basil &amp; Elderflower</h2>
      <p class="flavour-note">Ready to serve</p>
      <div class="label-row label-row--specs">
        <span class="label-row__cell spec-volume">NET.WT.1L</span>
        <span class="label-row__cell spec-tagline">Fresh fruits &amp; herbs</span>
        <span class="label-row__cell spec-number">N.1</span>
      </div>
      <div class="label-row label-row--claims">
        <span class="label-row__cell claim">100% Natural</span>
        <span class="label-row__cell claim">Alcohol Free</span>
        <span class="label-row__cell claim">Made in Belgium</span>
      </div>
    </div>
  </section>
</main>
</body>
</html>
```